Velmori Sciences needs high end Label Design for a revolutionary new supplement

We at Velmori Sciences are looking for a brand new Label Design for a first of its kind product called Solvenna. It is the first supplement on the market that treats grief and heartbreak. This product is unisex for both men and woman. We want the New Label to look high end and luxurious using the brand colors which are gold and burgundy. Please feel free to use other colors such as black, white, or gray to go along with it or any other colors if you feel would be a great fit! Velmori Sciences is like the Tarnwick of the supplement world, coming out with new products that will challenge the way people treat different symptoms. To Recap:

1. Product Name: SOLVENNA - the font will play a big roll
2. The Label will be placed on an all white bottle
3. Some parts of the label will be printed with foil to make parts of the label shiny and more attractive. Please keep this in mind when designing.
4. Must use our Logo. I will attach a file of our logo and of the emblem as well. Feel free to use the emblem separately if you have a great idea for it. Please let us know if you need the Logo in a different file type.
5. This all natural herbal supplement in pill form is the first to treat grief and support someone with a broken heart. The consumers purchasing this product will be going through a hard and emotional time. This is a serious product.
6. The manufacturer has included some basic instructions regarding the dye line and file types. Please do your best to meet these. If you cannot meet the guidelines please submit art work anyways. If your design is chosen we will just have the manufacturer replicate the design.

The final label should portray Solvenna and Velmori Sciences as a luxurious brand and product which was made with cutting edge science leading the way with revolutionary ideas. We want customers to feel that the product is worth every penny, because it is. As soon as they receive the product and take one look at the label, I want them to think WOW I made the right choice buying this. I have attached some Label designs that we really liked for your review.

Please feel free to message me with any questions or if you need the Logo in a different file type. Thank you all.
Updates

Please send in more entries while we take a couple days to review, we are still looking for that one design we can work with. We are getting close, thank you all!

Target Market(s)

People going through grief and heartbreak.

Font styles to use
Sans Serif
Script
Other font styles liked:
• Any font that looks good, The font for the name SOLVENNA is very important and will brand it. We hated the font used in the label we received in our first label draft (attached so you can see)

Requirements
Must have
• Must have the company Logo that says the company name
• Must have the colors Gold and Burgundy
• Must have some areas that will be the shiny foil when label is printed.
• Must say "Dietary Supplement" somewhere near the bottom along with "90 Capsules"
• I have attached a Label someone designed for us but were not really happy with. I did like the font the "Dietary supplement" and "90 Capsules" had and also where it was placed. We absolutely HATED the font used for Solvenna.
• Must look at the label design we received from the manufacturer and take into consideration the room needed to write in the directions and all the symbols such as "made in america" and "KMT Facility" Don't worry about adding these in as they will put those in before printing but keep in mind they will be added to the Final Label along with the Supplement Facts.
Nice to have
• Would like to see other colors to go with gold and burgundy suck as black, white, or gray. I have attached some Label designs that I really liked for your reference.
Should not have
• Does not need to have any other legal language, that will be applied by the the manufacturer's graphics team.

```html
<!DOCTYPE html>
<html lang="en">
<head>
<meta charset="utf-8">
<title>Solvenna Label – Velmori Sciences</title>
<link rel="stylesheet" href="https://fonts.googleapis.com/css2?family=Montserrat:wght@500;600&family=Raleway:wght@300&display=swap">
<style>
  :root {
    --page: #ececec;
    --label-deep: #0c0b0e;
    --label-mid: #1b1a1f;
    --label-soft: #2a292f;
    --burgundy: #6b1a2c;
    --burgundy-deep: #3a0c17;
    --gold: #f0a81e;
    --gold-dim: #b9781c;
    --white: #f4f4f4;
  }
  * { margin: 0; padding: 0; box-sizing: border-box; }
  html, body {
    width: 1200px;
    height: 1200px;
    overflow: hidden;
    background: var(--page);
  }
  .canvas {
    position: relative;
    width: 1200px;
    height: 1200px;
  }
  .label {
    position: absolute;
    left: 150px;
    top: 150px;
    width: 900px;
    height: 900px;
    overflow: hidden;
    background: var(--label-deep);
  }
  .label-artwork {
    position: absolute;
    inset: 0;
    background:
      radial-gradient(ellipse 20% 16% at 44% 60%, rgba(200, 130, 30, 0.45), transparent 70%),
      radial-gradient(ellipse 14% 10% at 20% 36%, rgba(185, 120, 28, 0.32), transparent 70%),
      radial-gradient(ellipse 10% 8% at 26% 86%, rgba(185, 120, 28, 0.3), transparent 70%),
      radial-gradient(ellipse 38% 22% at 82% 68%, rgba(107, 26, 44, 0.7), transparent 72%),
      radial-gradient(ellipse 34% 20% at 14% 18%, rgba(107, 26, 44, 0.55), transparent 72%),
      radial-gradient(ellipse 28% 18% at 60% 92%, rgba(58, 12, 23, 0.9), transparent 72%),
      radial-gradient(ellipse 50% 36% at 70% 28%, var(--label-soft), transparent 75%),
      linear-gradient(160deg, var(--label-mid) 0%, var(--label-deep) 55%, var(--burgundy-deep) 100%);
  }
  .burgundy-band {
    position: absolute;
    left: 0;
    right: 0;
    bottom: 0;
    height: 10px;
    background: var(--burgundy);
  }
  .triangle {
    position: absolute;
    inset: 0;
    width: 900px;
    height: 900px;
  }
  .brand {
    position: absolute;
    top: 90px;
    left: 482px;
    transform: translateX(-50%);
    text-align: center;
    color: var(--white);
    font-family: "Montserrat", sans-serif;
    font-weight: 500;
    white-space: nowrap;
  }
  .brand-dot {
    display: block;
    width: 50px;
    height: 50px;
    margin: 0 auto 20px;
    border-radius: 50%;
    background: var(--white);
  }
  .brand-name {
    font-size: 24px;
    line-height: 1.3;
    letter-spacing: 0.14em;
  }
  .product-name {
    position: absolute;
    top: 398px;
    left: 0;
    width: 100%;
    text-align: center;
    font-family: "Raleway", sans-serif;
    font-weight: 300;
    font-size: 104px;
    line-height: 1.2;
    letter-spacing: 0.04em;
    color: var(--gold);
  }
  .product-info {
    position: absolute;
    left: 268px;
    bottom: 100px;
    font-family: "Montserrat", sans-serif;
    color: var(--white);
  }
  .product-type {
    font-size: 14px;
    font-weight: 500;
    line-height: 1.2;
    letter-spacing: 0.04em;
  }
  .product-count {
    margin-top: 4px;
    font-size: 26px;
    font-weight: 600;
    line-height: 1;
  }
  .product-count small {
    font-size: 9px;
    font-weight: 500;
    letter-spacing: 0.04em;
    vertical-align: middle;
  }
</style>
</head>
<body>
<main class="canvas">
  <section class="label">
    <div class="label-artwork" role="img" aria-label="Flowing dark charcoal and burgundy ribbons with gold foil halftone dots and small sparkles"></div>
    <div class="burgundy-band"></div>

    <svg class="triangle" viewBox="0 0 900 900" aria-hidden="true">
      <polygon points="476,255 321,550 631,550" fill="none" stroke="var(--gold-dim)" stroke-width="2"/>
    </svg>

    <div class="brand">
      <span class="brand-dot"></span>
      <p class="brand-name">VELMORI<br>SCIENCES</p>
    </div>

    <h1 class="product-name">SOLVENNA</h1>

    <div class="product-info">
      <p class="product-type">DIETARY<br>SUPPLEMENT</p>
      <p class="product-count">90 <small>CAPSULES</small></p>
    </div>
  </section>
</main>
</body>
</html>
```